AI Business Tools Landing Page

My web-based website builder (Pavlora.com) will be adding many new features in the very near future and I need an eye-catching landing page to promote these new products.

The page will have a primary section of the 8 main products we are promoting:
1. AI Instant Website Generator
2. AI Chatbot
3. Online Store Builder with AI Assistance
4. AI Auto-Blogging System
5. Online Scheduling System
6. Custom Email System
7. SEO Service
8. CRM System

The page will also have a smaller section for links to our affiliate programs. These can be smaller, less-promanent buttons or links. These are the affiliate products:
1. Get Your LLC
2. Website Design and Maintenance
3. Quorra Ads Management
4. Social Media Posting Service
5. Logo Design
6. Trademark Registration
7. Patent Application
8. Printing Services (including postcards, flyers, and merch.)
9. Bulk AI Content Generator

The theme and color scheme of the page should follow the theme of our main website, which is https://pavlora.com.

I need the page fully coded and ready to deploy on my server.

I look forward to seeing your amazing designs!

```html
<!DOCTYPE html>
<html lang="en">
<head>
<meta charset="utf-8">
<title>Pavlora – AI Website Builder</title>
<link rel="stylesheet" href="https://fonts.googleapis.com/css2?family=Poppins:wght@600;700;800&family=Roboto:wght@400;500;700&display=swap">
<style>
  :root {
    --blue: #0a74df;
    --blue-deep: #0a5fc9;
    --cyan: #29b3e6;
    --ink: #111418;
    --muted: #5b6470;
    --page: #eef5fb;
    --white: #ffffff;
    --line: #1f8fdc;
  }
  * { box-sizing: border-box; margin: 0; padding: 0; }
  html, body { width: 696px; height: 1200px; overflow: hidden; }
  body {
    position: relative;
    background: linear-gradient(180deg, var(--page) 0%, #f6fafd 60%, var(--page) 100%);
    font-family: "Roboto", sans-serif;
    color: var(--ink);
  }
  .abs { position: absolute; }

  /* hero */
  .hero-visual {
    position: absolute; left: 0; top: 0; width: 696px; height: 372px;
    background:
      radial-gradient(ellipse at 78% 40%, rgba(120,200,255,.75) 0%, rgba(40,120,230,.35) 30%, transparent 55%),
      radial-gradient(ellipse at 25% 55%, rgba(20,40,90,.9) 0%, transparent 50%),
      linear-gradient(120deg, #0b2a6b 0%, #0c4fb8 45%, #1c7fe0 70%, #0a3a8f 100%);
  }
  .hero-wave { position: absolute; left: 0; top: 280px; width: 696px; height: 100px; }
  .brand {
    position: absolute; display: flex; align-items: center; gap: 8px;
    font-family: "Roboto", sans-serif; font-weight: 500; letter-spacing: .2px;
  }
  .brand-dot { width: 30px; height: 30px; border-radius: 50%; }
  .brand--top { left: 64px; top: 17px; color: var(--white); font-size: 22px; }
  .brand--top .brand-dot { background: var(--white); }
  .menu-btn {
    position: absolute; left: 606px; top: 20px; width: 28px; height: 26px;
    background: linear-gradient(135deg, var(--cyan), var(--blue));
    border-radius: 2px 10px 2px 2px;
    display: flex; flex-direction: column; justify-content: center; align-items: center; gap: 2.5px;
  }
  .menu-btn span { width: 11px; height: 2px; background: var(--white); }
  .hero-title {
    position: absolute; left: 0; top: 110px; width: 696px; text-align: center;
    font-family: "Roboto", sans-serif; font-weight: 700; color: var(--white);
    font-size: 31px; line-height: 35px; text-shadow: 0 2px 8px rgba(0,30,80,.45);
  }
  .hero-sub {
    position: absolute; left: 0; top: 189px; width: 696px; text-align: center;
    font-family: "Poppins", sans-serif; font-weight: 600; color: var(--white);
    font-size: 13.5px; letter-spacing: 4.6px;
  }
  .cta {
    position: absolute; left: 296px; top: 220px; width: 108px; height: 27px;
    background: var(--blue); border: 1px solid var(--white);
    border-radius: 0 12px 0 12px;
    color: var(--white); font-family: "Poppins", sans-serif; font-weight: 700; font-size: 8.5px;
    display: flex; align-items: center; justify-content: center; gap: 5px; text-decoration: none;
  }
  .cta-arrow { width: 8px; height: 8px; border-radius: 50%; background: var(--white); position: relative; }
  .cta-arrow::after {
    content: ""; position: absolute; left: 2px; top: 2px; width: 3px; height: 3px;
    border-right: 1.2px solid var(--blue); border-top: 1.2px solid var(--blue); transform: rotate(45deg);
  }
  .badge {
    position: absolute; left: 329px; top: 312px; width: 42px; height: 42px; border-radius: 50%;
    background: var(--white); box-shadow: 0 4px 10px rgba(10,80,160,.25);
    display: flex; align-items: center; justify-content: center;
  }
  .badge span { width: 24px; height: 24px; border-radius: 50%; background: linear-gradient(135deg, var(--blue), var(--cyan)); }

  /* section heading */
  .section-title {
    position: absolute; left: 0; width: 696px; text-align: center;
    font-family: "Poppins", sans-serif; font-weight: 800; font-size: 20px;
  }
  .section-title::after {
    content: ""; display: block; width: 39px; height: 2px; margin: 4px auto 0;
    background: var(--blue);
  }
  .products-title { top: 402px; color: var(--ink); }

  /* product map */
  .hub {
    position: absolute; left: 93px; top: 514px; width: 196px; height: 196px; border-radius: 50%;
    background: radial-gradient(circle at 45% 45%, #ffffff 0%, #f3f8fc 100%);
    box-shadow: 0 0 0 1px rgba(31,143,220,.12), 0 6px 18px rgba(10,80,160,.08);
  }
  .hub-core {
    position: absolute; left: 146px; top: 567px; width: 90px; height: 90px; border-radius: 50%;
    background: linear-gradient(135deg, var(--blue), var(--cyan));
    box-shadow: 0 0 0 3px #e9f3fb, 0 0 0 4px rgba(31,143,220,.3);
  }
  .connectors { position: absolute; left: 0; top: 0; width: 696px; height: 800px; }
  .node {
    position: absolute; width: 42px; height: 42px; border-radius: 50%;
    background: linear-gradient(135deg, var(--blue-deep), var(--cyan));
    box-shadow: 0 3px 8px rgba(10,80,160,.2);
  }
  .node::after {
    content: ""; position: absolute; left: 12px; top: 12px; width: 18px; height: 18px;
    border: 1.5px solid var(--white); border-radius: 4px;
  }
  .node--light { background: linear-gradient(135deg, #2ca7e6, #39bdf0); }
  .product-name {
    position: absolute; font-weight: 500; font-size: 8.2px; color: var(--ink); white-space: nowrap;
  }
  .product-desc {
    position: absolute; font-size: 7.8px; color: var(--muted); white-space: nowrap; line-height: 13.5px;
  }

  /* affiliate band */
  .band {
    position: absolute; left: 0; top: 780px; width: 696px; height: 340px;
    background:
      radial-gradient(ellipse at 50% 40%, rgba(255,255,255,.12) 0%, transparent 45%),
      linear-gradient(100deg, #0962d8 0%, #0a78e2 50%, #27b4e8 100%);
  }
  .band-wave { position: absolute; left: 0; width: 696px; }
  .affiliate-title { top: 872px; color: var(--white); }
  .affiliate-title::after { background: var(--white); }
  .aff-card { position: absolute; top: 932px; width: 126px; height: 118px; }
  .aff-card svg { position: absolute; left: 0; top: 0; }
  .aff-label {
    position: absolute; left: 0; width: 126px; text-align: center;
    font-weight: 500; font-size: 9.3px; line-height: 14px; color: var(--ink);
  }
  .slider-btn {
    position: absolute; width: 30px; height: 30px; border-radius: 50%; background: var(--white);
    display: flex; align-items: center; justify-content: center;
    font-size: 10px; font-weight: 700; color: var(--ink); box-shadow: 0 2px 6px rgba(0,40,100,.2);
  }

  /* footer */
  .brand--foot { left: 64px; top: 1146px; color: var(--ink); font-size: 22px; }
  .brand--foot .brand-dot { background: linear-gradient(135deg, var(--blue), var(--cyan)); }
  .copyright { position: absolute; left: 450px; top: 1154px; width: 183px; text-align: right; font-size: 7.6px; color: var(--ink); }
</style>
</head>
<body>

<header>
  <div class="hero-visual" role="img" aria-label="Photo of a businessman using a phone facing a glowing holographic AI figure with floating data screens"></div>
  <div class="brand brand--top"><span class="brand-dot"></span>Pavlora</div>
  <div class="menu-btn" aria-label="Menu"><span></span><span></span><span></span></div>
  <h1 class="hero-title">THE PREMIER<br>AI WEBSITE BUILDER</h1>
  <p class="hero-sub">GENERATE YOUR SITE NOW!</p>
  <a class="cta" href="https://pavlora.com">GET STARTED <span class="cta-arrow"></span></a>
  <svg class="hero-wave" viewBox="0 0 696 100" preserveAspectRatio="none">
    <path d="M0,48 C120,78 250,82 350,56 C450,28 560,12 696,62 L696,100 L0,100 Z" fill="#eef5fb"/>
    <path d="M55,63 C150,86 255,84 345,60" fill="none" stroke="#1777df" stroke-width="4"/>
    <path d="M360,52 C450,25 560,14 630,30" fill="none" stroke="#1f9ee6" stroke-width="3"/>
  </svg>
  <div class="badge"><span></span></div>
</header>

<main>
  <h2 class="section-title products-title">OUR PRODUCTS</h2>

  <div class="hub"></div>
  <div class="hub-core"></div>

  <svg class="connectors" viewBox="0 0 696 800">
    <g fill="none" stroke="#1f8fdc" stroke-width="1">
      <polyline points="219,517 246,491 277,491"/>
      <polyline points="261,541 275,528 338,528"/>
      <polyline points="283,577 297,562 392,562"/>
      <polyline points="289,608 303,594 438,594"/>
      <polyline points="289,625 302,638 438,638"/>
      <polyline points="279,655 293,669 388,669"/>
      <polyline points="251,688 265,702 324,702"/>
      <polyline points="204,707 233,736 269,736"/>
    </g>
    <g fill="#1f8fdc">
      <circle cx="219" cy="517" r="1.8"/><circle cx="261" cy="541" r="1.8"/>
      <circle cx="283" cy="577" r="1.8"/><circle cx="289" cy="608" r="1.8"/>
      <circle cx="289" cy="625" r="1.8"/><circle cx="279" cy="655" r="1.8"/>
      <circle cx="251" cy="688" r="1.8"/><circle cx="204" cy="707" r="1.8"/>
    </g>
  </svg>

  <div class="node" style="left:276px;top:469px"></div>
  <p class="product-name" style="left:325px;top:461px">AI INSTANT WEBSITE GENERATOR</p>
  <p class="product-desc" style="left:325px;top:473px">Get a professional, SEO-optimized website in seconds<br>Includes custom domain, secure high-speed hosting, professional images, and more!</p>

  <div class="node node--light" style="left:338px;top:504px"></div>
  <p class="product-name" style="left:385px;top:516px">AI CHATBOT</p>

  <div class="node" style="left:392px;top:540px"></div>
  <p class="product-name" style="left:438px;top:553px">ONLINE STORE BUILDER WITH AI ASSISTANCE</p>

  <div class="node node--light" style="left:438px;top:572px"></div>
  <p class="product-name" style="left:485px;top:589px">AI AUTO-BLOGGING SYSTEM</p>

  <div class="node" style="left:438px;top:620px"></div>
  <p class="product-name" style="left:484px;top:637px">ONLINE SCHEDULING SYSTEM</p>

  <div class="node node--light" style="left:388px;top:651px"></div>
  <p class="product-name" style="left:436px;top:672px">CUSTOM EMAIL SYSTEM</p>

  <div class="node" style="left:324px;top:687px"></div>
  <p class="product-name" style="left:371px;top:707px">SEO SERVICE</p>

  <div class="node node--light" style="left:269px;top:719px"></div>
  <p class="product-name" style="left:314px;top:738px">CRM SYSTEM</p>

  <section>
    <div class="band"></div>
    <svg class="band-wave" style="top:780px;height:60px" viewBox="0 0 696 60" preserveAspectRatio="none">
      <path d="M0,0 L696,0 L696,26 C560,4 360,10 150,30 C80,36 30,28 0,14 Z" fill="#eef5fb"/>
      <path d="M40,40 C200,42 420,18 630,22" fill="none" stroke="#ffffff" stroke-width="3"/>
    </svg>
    <svg class="band-wave" style="top:1070px;height:60px" viewBox="0 0 696 60" preserveAspectRatio="none">
      <path d="M0,26 C200,58 400,32 560,16 C630,10 670,18 696,24 L696,60 L0,60 Z" fill="#eef5fb"/>
      <path d="M0,32 C180,62 380,40 540,22" fill="none" stroke="#ffffff" stroke-width="2"/>
    </svg>

    <h2 class="section-title affiliate-title">AFFILIATE PRODUCTS</h2>

    <div class="slider-btn" style="left:24px;top:972px">«</div>
    <div class="slider-btn" style="left:642px;top:985px">»</div>

    <div class="aff-card" style="left:69px">
      <svg width="126" height="118" viewBox="0 0 126 118">
        <polygon points="34,6 92,6 120,59 92,112 34,112 6,59" fill="#ffffff" stroke="#ffffff" stroke-width="10" stroke-linejoin="round"/>
        <polygon points="37,11 89,11 115,59 89,107 37,107 11,59" fill="none" stroke="#7cc4ee" stroke-width=".6" stroke-dasharray="2 2" stroke-linejoin="round"/>
        <polygon points="43,0 83,0 83,22 63,28 43,22" fill="#0a74df"/>
      </svg>
      <p class="aff-label" style="top:80px">GET YOUR LLC</p>
    </div>

    <div class="aff-card" style="left:215px">
      <svg width="126" height="118" viewBox="0 0 126 118">
        <polygon points="34,6 92,6 120,59 92,112 34,112 6,59" fill="#ffffff" stroke="#ffffff" stroke-width="10" stroke-linejoin="round"/>
        <polygon points="37,11 89,11 115,59 89,107 37,107 11,59" fill="none" stroke="#7cc4ee" stroke-width=".6" stroke-dasharray="2 2" stroke-linejoin="round"/>
        <polygon points="43,0 83,0 83,22 63,28 43,22" fill="#29b3e6"/>
      </svg>
      <p class="aff-label" style="top:79px">LOGO DESIGN</p>
    </div>

    <div class="aff-card" style="left:361px">
      <svg width="126" height="118" viewBox="0 0 126 118">
        <polygon points="34,6 92,6 120,59 92,112 34,112 6,59" fill="#ffffff" stroke="#ffffff" stroke-width="10" stroke-linejoin="round"/>
        <polygon points="37,11 89,11 115,59 89,107 37,107 11,59" fill="none" stroke="#7cc4ee" stroke-width=".6" stroke-dasharray="2 2" stroke-linejoin="round"/>
        <polygon points="43,0 83,0 83,22 63,28 43,22" fill="#0a6fe0"/>
      </svg>
      <p class="aff-label" style="top:71px">WEBSITE DESIGN<br>&amp; MAINTENANCE</p>
    </div>

    <div class="aff-card" style="left:507px">
      <svg width="126" height="118" viewBox="0 0 126 118">
        <polygon points="34,6 92,6 120,59 92,112 34,112 6,59" fill="#ffffff" stroke="#ffffff" stroke-width="10" stroke-linejoin="round"/>
        <polygon points="37,11 89,11 115,59 89,107 37,107 11,59" fill="none" stroke="#7cc4ee" stroke-width=".6" stroke-dasharray="2 2" stroke-linejoin="round"/>
        <polygon points="43,0 83,0 83,22 63,28 43,22" fill="#29b3e6"/>
      </svg>
      <p class="aff-label" style="top:72px">QUORRA ADS<br>MANAGEMENT</p>
    </div>
  </section>
</main>

<footer>
  <div class="brand brand--foot"><span class="brand-dot"></span>Pavlora</div>
  <p class="copyright">Copyright@2024- All Rights Reserved</p>
</footer>

</body>
</html>
```